Verdel Harvest - Stationery Design Project

We need a stationary for our business. We grow roots and fruits in Central and South America, we import and distribute in FL, USA. We do fresh and frozen products.

Target Market(s)

Small and big supermarkets, wholesalers, traders, distributors, etc

Industry/Entity Type

Business

```html
<!DOCTYPE html>
<html lang="en">
<head>
<meta charset="utf-8">
<title>Verdel Harvest — Stationery</title>
<link href="https://fonts.googleapis.com/css2?family=Montserrat:wght@500&display=swap" rel="stylesheet">
<style>
  :root{
    --backdrop:#e6e6e4;
    --navy:#2e4677;
    --paper:#f8f8f8;
    --orange:#e0831f;
    --leaf:#56683a;
    --rule:#3a3a3a;
    --ink:#6d6d6d;
    --faint-on-navy:rgba(255,255,255,0.09);
    --faint-on-paper:rgba(0,0,0,0.035);
  }
  *{margin:0;padding:0;box-sizing:border-box}
  html,body{width:1200px;height:1000px;overflow:hidden}
  body{background:var(--backdrop);position:relative;font-family:"Montserrat",Arial,sans-serif}
  .piece{position:absolute;overflow:hidden}
  .brand-name{position:absolute;white-space:nowrap;font-weight:500;letter-spacing:0.01em;transform:translateX(-50%)}
  .faint-disc{position:absolute;border-radius:50%}

  /* Folder */
  .folder{left:190px;top:108px;width:385px;height:543px;background:var(--navy)}
  .folder .brand-name{left:50%;top:183px;font-size:34px;color:#fff}
  .folder .faint-disc{width:300px;height:300px;right:-90px;bottom:-110px;background:var(--faint-on-navy)}

  /* Letterhead */
  .letterhead{left:610px;top:122px;width:375px;height:529px;background:var(--paper)}
  .letterhead .brand-name{left:50%;top:34px;font-size:18px;color:var(--orange)}
  .letterhead .header-rule{position:absolute;left:0;right:0;top:75px;height:1px;background:var(--rule)}
  .letterhead .faint-disc{width:260px;height:260px;right:-70px;bottom:-90px;background:var(--faint-on-paper)}
  .letterhead .footer-band{position:absolute;left:0;right:0;bottom:0;height:8px;background:var(--navy)}
  .contact{position:absolute;top:488px;font-size:6px;color:var(--ink);line-height:10px}
  .contact li{list-style:none;display:flex;align-items:center;gap:6px}
  .contact .dot{width:5px;height:5px;border-radius:50%;background:var(--leaf)}
  .contact.phones{left:17px}
  .contact.web{left:104px}
  .contact-divider{position:absolute;left:86px;top:488px;width:1px;height:20px;background:#aaa}

  /* Envelope */
  .envelope{left:190px;top:698px;width:392px;height:193px;background:var(--paper)}
  .envelope .flap{position:absolute;left:0;top:0}
  .envelope .brand-name{left:50%;top:13px;font-size:17px;color:#fff}

  /* Card */
  .card{left:618px;top:698px;width:391px;height:193px;background:var(--paper)}
  .card .brand-name{left:93px;top:34px;font-size:14px;color:var(--orange)}
  .card .faint-disc{width:170px;height:170px;right:-45px;bottom:-70px;background:var(--faint-on-paper)}
  .card .footer-band{position:absolute;left:0;right:0;bottom:0;height:7px;background:var(--navy)}
</style>
</head>
<body>

<section class="piece folder" aria-label="Presentation folder">
  <span class="brand-name">Verdel Harvest</span>
  <span class="faint-disc"></span>
</section>

<section class="piece letterhead" aria-label="Letterhead">
  <span class="brand-name">Verdel Harvest</span>
  <div class="header-rule"></div>
  <span class="faint-disc"></span>
  <ul class="contact phones">
    <li><span class="dot"></span>0401 555 218</li>
    <li><span class="dot"></span>0471 555 306</li>
  </ul>
  <div class="contact-divider"></div>
  <ul class="contact web">
    <li><span class="dot"></span>www.verdelharvest.com</li>
    <li><span class="dot"></span>support@verdelharvest.com</li>
  </ul>
  <div class="footer-band"></div>
</section>

<section class="piece envelope" aria-label="Envelope">
  <svg class="flap" width="392" height="58" viewBox="0 0 392 58">
    <path d="M0 0H392V30Q392 57 362 57H30Q0 57 0 30Z" fill="var(--navy)"/>
  </svg>
  <span class="brand-name">Verdel Harvest</span>
</section>

<section class="piece card" aria-label="Business card">
  <span class="brand-name">Verdel Harvest</span>
  <span class="faint-disc"></span>
  <div class="footer-band"></div>
</section>

</body>
</html>
```